KRT Project Signage

Need a sign to be displayed in the front of properties currently under Construction or Renovation to advertise our company information. Need it to be Professional and Contemporary. We are a Design/Build Construction Company. Information should include Company Name, email, website, phone number. Attached: Logo and company brochure, also included and inspiration images

```html
<!DOCTYPE html>
<html lang="en">
<head>
<meta charset="utf-8">
<title>KRT Project Signage</title>
<link rel="stylesheet" href="https://fonts.googleapis.com/css2?family=Oswald:wght@600&family=Poiret+One&family=Poppins:wght@400;500;700;800&family=Montserrat:wght@600&display=swap">
<style>
  :root {
    --bg: #9aa1a8;
    --yellow: #f2ea45;
    --white: #ffffff;
    --black: #0a0a0a;
    --navy: #0c1f29;
    --ink: #262626;
  }
  html, body {
    margin: 0;
    padding: 0;
    width: 1200px;
    height: 2400px;
    overflow: hidden;
    background: var(--bg);
  }
  .sign {
    position: absolute;
    left: 100px;
    top: 450px;
    width: 1000px;
    height: 1500px;
    box-shadow: 0 20px 40px rgba(0,0,0,0.35);
  }
  .sign svg { display: block; width: 1000px; height: 1500px; }
  .brand-name { font-family: "Poiret One", sans-serif; font-size: 60px; fill: var(--black); letter-spacing: 1px; }
  .person-name { font-family: "Oswald", sans-serif; font-weight: 600; font-size: 170px; fill: var(--navy); }
  .role { font-family: "Montserrat", sans-serif; font-weight: 600; font-size: 46px; fill: var(--white); letter-spacing: 9px; }
  .address { font-family: "Poppins", sans-serif; font-weight: 400; font-size: 49px; fill: var(--ink); }
  .email { font-family: "Poppins", sans-serif; font-weight: 400; font-size: 50px; fill: var(--ink); }
  .office-label { font-family: "Poppins", sans-serif; font-weight: 800; font-size: 56px; fill: var(--yellow); letter-spacing: 3px; }
  .office-number { font-family: "Poppins", sans-serif; font-weight: 700; font-size: 62px; fill: var(--yellow); }
  .mobile-number { font-family: "Poppins", sans-serif; font-weight: 800; font-size: 120px; fill: var(--black); }
</style>
</head>
<body>
<div class="sign">
  <svg viewBox="0 0 1000 1500" xmlns="http://www.w3.org/2000/svg">
    <defs>
      <path id="handset" d="M6.6 10.8c1.4 2.8 3.8 5.1 6.6 6.6l2.2-2.2c.3-.3.7-.4 1-.2 1.1.4 2.3.6 3.6.6.6 0 1 .4 1 1V20c0 .6-.4 1-1 1C10.6 21 3 13.4 3 4c0-.6.4-1 1-1h3.5c.6 0 1 .4 1 1 0 1.3.2 2.5.6 3.6.1.3 0 .7-.2 1L6.6 10.8z"/>
    </defs>

    <!-- panels -->
    <rect class="panel-white" x="0" y="0" width="1000" height="1500" fill="var(--white)"/>
    <rect class="panel-yellow" x="0" y="0" width="1000" height="800" fill="var(--yellow)"/>

    <!-- header arc -->
    <path class="header-crescent" fill="var(--black)"
      d="M70 78 C90 350 300 484 501 484 C702 484 912 350 932 78 C880 330 705 442 501 442 C297 442 122 330 70 78 Z"/>
    <ellipse class="header-bowl" cx="501" cy="0" rx="426" ry="420" fill="var(--white)"/>

    <!-- company name -->
    <circle class="brand-dot" cx="835" cy="158" r="16" fill="var(--yellow)"/>
    <text class="brand-name" x="480" y="198" text-anchor="middle">KRT CONSTRUCTION</text>

    <!-- person -->
    <text class="person-name" x="500" y="650" text-anchor="middle" textLength="820" lengthAdjust="spacingAndGlyphs">MARCUS DELANEY</text>
    <polygon class="role-ribbon" fill="var(--black)" points="125,668 875,668 842,705 875,741 125,741 158,705"/>
    <text class="role" x="500" y="722" text-anchor="middle">DESIGN &amp; BUILDER</text>

    <!-- address -->
    <circle cx="501" cy="806" r="40" fill="var(--white)"/>
    <circle cx="501" cy="806" r="33" fill="var(--yellow)"/>
    <path class="icon-pin" fill="var(--black)" d="M501 784c-10 0-18 8-18 18 0 13 18 30 18 30s18-17 18-30c0-10-8-18-18-18zm0 25a7 7 0 1 1 0-14 7 7 0 0 1 0 14z"/>
    <text class="address" x="495" y="900" text-anchor="middle">4510 SE 9th St., Ste. 310</text>
    <text class="address" x="495" y="960" text-anchor="middle">Coral Springs, FL 33065</text>

    <!-- email -->
    <circle cx="501" cy="1024" r="33" fill="var(--yellow)"/>
    <g class="icon-mail" fill="none" stroke="var(--black)" stroke-width="3.5">
      <rect x="481" y="1011" width="40" height="27"/>
      <path d="M481 1011 L501 1027 L521 1011 M481 1038 L496 1023 M521 1038 L506 1023"/>
    </g>
    <text class="email" x="500" y="1106" text-anchor="middle">dana@krtconstruction.com</text>

    <!-- office line -->
    <rect class="office-bar" x="72" y="1169" width="832" height="90" rx="14" fill="var(--black)"/>
    <text class="office-label" x="111" y="1234" textLength="225" lengthAdjust="spacingAndGlyphs">OFFICE</text>
    <circle cx="383" cy="1214" r="36" fill="var(--white)"/>
    <circle cx="383" cy="1214" r="28" fill="var(--black)"/>
    <use href="#handset" fill="var(--white)" transform="translate(366 1197) scale(1.4)"/>
    <text class="office-number" x="435" y="1236" textLength="445" lengthAdjust="spacingAndGlyphs">555.210.4387</text>

    <!-- mobile line -->
    <circle cx="128" cy="1351" r="49" fill="var(--black)"/>
    <circle cx="128" cy="1351" r="41" fill="var(--yellow)"/>
    <use href="#handset" fill="var(--black)" transform="translate(106 1329) scale(1.85)"/>
    <text class="mobile-number" x="195" y="1393" textLength="710" lengthAdjust="spacingAndGlyphs">555.318.6042</text>
  </svg>
</div>
</body>
</html>
```